K7 Electrical Services Ltd Web design

I require a web site for my new electrical contracting company. We are customer service orientated. Offering high value electrical installations, design and maintenance. Focused on custom residential and commercial upgrading. Lighting design and application are paramount in our company's services. Industry leading product use and integration are always on the forefront with our customer client services. As well as energy efficiency.

Target Market(s)

Homebuilders, General Contractors, Property management companies, clients, individuals,

Industry/Entity Type

Electric Company

Coding

Coded - Design and coding required

Number of Pages Required

3 page

Requirements
Must have
• Classic, modern, edgy but not trendy . Appeals to the masse.
• 3 page
• home page
• about page
• gallery page
• ability to contact from the webiste
Nice to have
• open to all types of designs that are relative to the construction industry.
• Black, Grey, metallic ice blue and deep purple colours from the logo.
Should not have
• anything cheesy with cartoon light bulb images.

```html
<!DOCTYPE html>
<html lang="en">
<head>
<meta charset="utf-8">
<title>K7 Electrical Services Ltd</title>
<link rel="stylesheet" href="https://fonts.googleapis.com/css2?family=Questrial&family=Open+Sans:wght@400;600;700&display=swap">
<style>
:root{
  --purple:#5b2a88;
  --grey:#77787b;
  --grey-light:#f1f1f1;
  --ink:#222;
  --text:#333;
  --white:#fff;
  --footer-bar:#4a4a4a;
}
*{box-sizing:border-box;margin:0;padding:0}
html,body{width:1200px;height:3237px;overflow:hidden}
body{position:relative;background:var(--white);font-family:"Open Sans",Arial,sans-serif;color:var(--text)}
.abs{position:absolute}
.company-name{font-family:"Open Sans",Arial,sans-serif;font-weight:600;color:var(--purple);white-space:nowrap;letter-spacing:0}
.heading{font-family:"Questrial",sans-serif;font-size:36px;font-weight:700;letter-spacing:1px;text-align:center;color:var(--purple)}
.heading .soft{color:#9a9a9a}
.underline{position:absolute;height:4px;width:110px;left:50%;transform:translateX(-50%)}
.underline::before{content:"";position:absolute;left:0;top:0;width:55px;height:4px;background:var(--purple)}
.underline::after{content:"";position:absolute;right:0;top:0;width:55px;height:4px;background:#b5b5b5}

/* header */
.site-header{top:0;left:0;width:1200px;height:86px}
.site-header .company-name{position:absolute;left:142px;top:30px;font-size:22px}
.header-cta{right:142px;top:16px;font-family:"Questrial",sans-serif;font-weight:700;font-size:15px;color:var(--purple)}
.main-nav{right:142px;top:52px;display:flex;gap:44px;font-family:"Questrial",sans-serif;font-size:15px;font-weight:700;color:var(--ink)}
.main-nav .active{color:var(--purple)}

/* hero */
.hero{top:86px;left:0;width:1200px;height:512px;background:linear-gradient(100deg,#f4f1ec 0%,#e7e1d8 45%,#c9bba8 75%,#8c7a66 100%)}
.hero h1{position:absolute;left:142px;top:184px;width:480px;font-family:"Questrial",sans-serif;font-weight:400;font-size:30px;line-height:45px;color:var(--ink);white-space:nowrap}
.hero .arrow{position:absolute;top:242px;width:26px;height:26px;background:#333;display:flex;align-items:center;justify-content:center}

/* services band */
.band{top:598px;height:205px;width:600px}
.band.res{left:0;background:var(--purple)}
.band.com{left:600px;background:var(--grey)}
.band h3{position:absolute;top:18px;font-family:"Questrial",sans-serif;font-size:25px;color:var(--white);font-weight:700;display:flex;align-items:center;gap:14px}
.band p{position:absolute;top:70px;width:310px;font-size:11px;line-height:19px;color:var(--white)}
.band .rule{position:absolute;top:60px;height:1px;width:310px;background:rgba(255,255,255,.35)}
.band-badge{left:508px;top:606px;width:184px;height:184px;border-radius:50%;background:var(--white);border:10px solid #d7d7d7;display:flex;align-items:center;justify-content:center;text-align:center}
.band-badge .company-name{font-size:15px;line-height:20px;white-space:normal;width:120px}

/* intro */
.intro-brand{left:0;width:1200px;top:860px;text-align:center}
.intro-brand .company-name{font-size:28px}
.intro-text{left:180px;width:840px;top:942px;text-align:center;font-size:14px;line-height:24px;color:var(--ink)}
.service-card{top:1068px;width:281px;height:145px;border:1px solid #e2e2e2;background:var(--white)}
.service-card .hex{position:absolute;left:50%;top:-54px;transform:translateX(-50%)}
.service-card h4{position:absolute;top:56px;left:0;width:100%;text-align:center;font-family:"Questrial",sans-serif;font-weight:400;font-size:21px;line-height:25px;color:#444}

/* about */
.about{top:1262px;left:0;width:1200px;height:387px;background:var(--grey-light)}
.about .title{position:absolute;top:48px;left:0;width:1200px;display:flex;justify-content:center;align-items:baseline;gap:14px}
.about .title .company-name{font-size:26px;color:var(--grey)}
.about .underline{top:104px}
.about p{position:absolute;left:142px;width:916px;text-align:center;font-size:11px;line-height:19px;color:var(--ink)}
.btn{display:inline-flex;align-items:center;justify-content:center;background:var(--purple);color:var(--white);font-family:"Questrial",sans-serif;font-weight:700;border-radius:6px}
.about .btn{position:absolute;left:503px;top:292px;width:194px;height:43px;font-size:20px}

/* gallery */
.gallery-title{top:1694px;left:0;width:1200px}
.gallery-title .underline{top:52px}
.tile{position:absolute}
.tile.feature{background:linear-gradient(160deg,#5a5650,#2e2c2a)}
.tile.feature h5{position:absolute;top:64px;left:0;width:100%;text-align:center;font-family:"Questrial",sans-serif;color:var(--white);font-size:21px;line-height:26px;font-weight:700}
.tile.feature p{position:absolute;top:120px;left:22px;width:292px;text-align:center;color:#eee;font-size:11px;line-height:18px}

/* why */
.why{top:2320px;left:0;width:1200px;height:231px;background:var(--grey-light)}
.why .heading{position:absolute;top:44px;left:0;width:1200px}
.why .underline{top:96px}
.why p{position:absolute;top:112px;left:0;width:1200px;text-align:center;font-size:16px;line-height:24px;color:var(--ink)}
.why .link{position:absolute;top:170px;left:0;width:1200px;text-align:center;font-family:"Questrial",sans-serif;font-weight:700;font-size:16px;color:var(--purple)}

/* contact */
.contact-title{top:2596px;left:0;width:1200px}
.contact-title .underline{top:52px}
.field{position:absolute;left:170px;width:380px;border:2px solid #b9a6d1;border-radius:10px;background:var(--white);font-size:16px;color:#444;padding:10px 14px}
.field .req{color:#b02020}
.contact-form .btn{position:absolute;left:173px;top:2959px;width:144px;height:43px;font-size:22px;border-radius:4px}
.contact-info{left:615px;top:2696px;width:443px}
.contact-info h3{font-family:"Questrial",sans-serif;font-weight:700;font-size:26px;color:var(--purple)}
.contact-info .rule{height:1px;background:#ccc;margin:8px 0 10px}
.contact-info p{font-size:16px;line-height:28px;color:#444}
.map{left:615px;top:2814px;width:443px;height:134px;border:1px solid #ccc;background:linear-gradient(135deg,#eef0ea,#dfe6d8 60%,#cfe0c6)}

/* footer */
.site-footer{top:3053px;left:0;width:1200px;height:141px;background:var(--purple)}
.footer-nav{position:absolute;top:28px;left:0;width:1200px;display:flex;justify-content:center;gap:36px;font-size:12px;color:var(--white)}
.site-footer .company-name{position:absolute;top:74px;left:0;width:1200px;text-align:center;color:var(--white);font-size:24px}
.copyright{top:3194px;left:0;width:1200px;height:43px;background:var(--footer-bar);color:#ddd;font-size:11px;display:flex;align-items:center;justify-content:center}
</style>
</head>
<body>

<header class="site-header abs">
  <div class="company-name">K7 Electrical Services Ltd</div>
  <div class="header-cta abs">SCHEDULE YOUR SERVICE TODAY</div>
  <nav class="main-nav abs"><span class="active">HOME</span><span>ABOUT US</span><span>GALLERY</span><span>CONTACT US</span></nav>
</header>

<section class="hero abs" role="img" aria-label="Photo of an electrician on a ladder installing a chandelier in a bright living room">
  <h1>We Are Customer Service<br>Orientated. Offering High<br>Value Electrical Installations,<br>Design And Maintenance</h1>
  <span class="arrow" style="left:6px"><svg width="12" height="12" viewBox="0 0 12 12"><path d="M8 1 3 6l5 5" fill="none" stroke="#fff" stroke-width="2"/></svg></span>
  <span class="arrow" style="right:6px"><svg width="12" height="12" viewBox="0 0 12 12"><path d="M4 1l5 5-5 5" fill="none" stroke="#fff" stroke-width="2"/></svg></span>
</section>

<section class="band res abs">
  <h3 style="left:148px"><svg width="42" height="40" viewBox="0 0 42 40" fill="none" stroke="#fff" stroke-width="2"><path d="M3 20 21 4l18 16"/><path d="M8 16v22h26V16"/><rect x="13" y="22" width="6" height="6"/><rect x="23" y="22" width="6" height="6"/></svg>Residential</h3>
  <div class="rule" style="left:148px"></div>
  <p style="left:148px">Lorem ipsum dolor sit amet, consectetuer adipiscing elit, sed diam nonummy nibh euismod tincidunt ut laoreet dolore magna aliquam erat volutpat. Ut wisi enim ad minim veniam, quis nostrud exerci tation ullamcorper suscipit lobortis nisl ut aliquip ex ea commodo consequat.</p>
</section>
<section class="band com abs">
  <h3 style="left:138px"><svg width="42" height="40" viewBox="0 0 42 40" fill="none" stroke="#fff" stroke-width="2"><rect x="4" y="14" width="14" height="24"/><rect x="18" y="4" width="18" height="34"/><path d="M22 10h10M22 16h10M22 22h10M22 28h10M8 20h6M8 26h6"/></svg>Commerical</h3>
  <div class="rule" style="left:140px"></div>
  <p style="left:140px">Lorem ipsum dolor sit amet, consectetuer adipiscing elit, sed diam nonummy nibh euismod tincidunt ut laoreet dolore magna aliquam erat volutpat. Ut wisi enim ad minim veniam, quis nostrud exerci tation ullamcorper suscipit lobortis nisl ut aliquip ex ea commodo consequat.</p>
</section>
<div class="band-badge abs"><span class="company-name">K7 Electrical Services Ltd</span></div>

<div class="intro-brand abs"><span class="company-name">K7 Electrical Services Ltd</span></div>
<p class="intro-text abs">We are customer service orientated. Offering high value text of the printing and typesetting industry. Lorem Ipsum has been the industry's standard dummy text ever since the 1500s.</p>

<article class="service-card abs" style="left:142px">
  <svg class="hex" width="92" height="100" viewBox="0 0 92 100"><polygon points="46,2 90,26 90,74 46,98 2,74 2,26" fill="var(--purple)"/><g fill="#fff"><rect x="38" y="28" width="4" height="12"/><rect x="50" y="28" width="4" height="12"/><path d="M32 40h28v10a14 14 0 0 1-28 0z"/><rect x="43" y="62" width="6" height="12"/></g></svg>
  <h4>Electrical<br>Installations</h4>
</article>
<article class="service-card abs" style="left:460px">
  <svg class="hex" width="92" height="100" viewBox="0 0 92 100"><polygon points="46,2 90,26 90,74 46,98 2,74 2,26" fill="var(--purple)"/><g stroke="#fff" stroke-width="6" stroke-linecap="round"><path d="M30 32l32 36"/><path d="M62 32 30 68"/></g><circle cx="30" cy="32" r="7" fill="#fff"/></svg>
  <h4>Design And<br>Maintenance</h4>
</article>
<article class="service-card abs" style="left:777px">
  <svg class="hex" width="92" height="100" viewBox="0 0 92 100"><polygon points="46,2 90,26 90,74 46,98 2,74 2,26" fill="var(--purple)"/><circle cx="46" cy="50" r="11" fill="#fff"/><g stroke="#fff" stroke-width="3" stroke-linecap="round"><path d="M46 28v6M46 66v6M24 50h6M62 50h6M31 35l4 4M61 35l-4 4M31 65l4-4M61 65l-4-4"/></g></svg>
  <h4>Lighting Design And<br>Application</h4>
</article>

<section class="about abs">
  <div class="title"><span class="heading">ABOUT</span><span class="company-name">K7 Electrical Services Ltd</span></div>
  <div class="underline"></div>
  <p style="top:124px">Lorem ipsum dolor sit amet, consectetuer adipiscing elit, sed diam nonummy nibh euismod tincidunt ut laoreet dolore magna aliquam erat volutpat. Ut wisi enim ad minim veniam, quis nostrud exerci tation ullamcorper suscipit lobortis nisl ut aliquip ex ea commodo consequat.</p>
  <p style="top:170px">Lorem ipsum dolor sit amet, consectetuer adipiscing elit, sed diam nonummy nibh euismod tincidunt ut laoreet dolore magna aliquam erat volutpat. Ut wisi enim ad minim veniam, quis nostrud exerci tation ullamcorper suscipit lobortis nisl ut aliquip ex ea commodo consequat. Duis autem vel eum iriure dolor in hendrerit in vulputate velit esse molestie consequat, vel illum dolore eu feugiat nulla facilisis at vero eros et accumsan et iusto odio dignissim qui blandit praesent luptatum zzril delenit augue duis dolore te feugait nulla facilisi. Duis autem vel eum iriure dolor in hendrerit in vulputate velit esse molestie consequat, vel illum dolore eu feugiat nulla facilisis at vero eros et accumsan et iusto odio dignissim qui blandit praesent luptatum zzril delenit augue duis dolore te feugait nulla facilisi.</p>
  <span class="btn">Call Us Today</span>
</section>

<section class="gallery-title abs">
  <div class="heading">WORK <span class="soft">GALLERY</span></div>
  <div class="underline"></div>
</section>
<div class="tile feature" style="left:142px;top:1780px;width:335px;height:287px" role="img" aria-label="Photo of exposed ceiling wiring at a construction site">
  <h5>Electrical<br>Installations</h5>
  <p>Lorem ipsum dolor sit amet, consectetuer adipiscing elit, sed diam nonummy nibh euismod tincidunt ut laoreet dolore magna aliquam erat volutpat. Ut wisi enim ad minim veniam, quis nostrud exerci tation ullamcorper suscipit lobortis nisl ut aliquip ex ea commodo consequat.</p>
</div>
<div class="tile" style="left:488px;top:1780px;width:326px;height:141px;background:linear-gradient(135deg,#e9e6e2,#c7c0b8)" role="img" aria-label="Photo of hands stripping coloured wires with pliers"></div>
<div class="tile" style="left:488px;top:1927px;width:157px;height:140px;background:linear-gradient(180deg,#6b4a2e,#c89a64)" role="img" aria-label="Photo of a staircase with warm step lighting"></div>
<div class="tile" style="left:656px;top:1927px;width:158px;height:140px;background:linear-gradient(135deg,#c9ccd0,#8d939a)" role="img" aria-label="Photo of hands working on a circuit breaker panel"></div>
<div class="tile" style="left:822px;top:1780px;width:236px;height:287px;background:linear-gradient(160deg,#e6ddd0,#a89882)" role="img" aria-label="Photo of an electrician fitting a ceiling light"></div>
<div class="tile" style="left:142px;top:2078px;width:503px;height:192px;background:linear-gradient(120deg,#e8ebee,#9aa3ab 70%,#5f6a73)" role="img" aria-label="Photo of a technician testing a distribution board with a multimeter"></div>
<div class="tile" style="left:656px;top:2078px;width:402px;height:192px;background:linear-gradient(135deg,#3a2618,#a0683a 60%,#d9a870)" role="img" aria-label="Photo of a modern kitchen with warm ambient lighting"></div>

<section class="why abs">
  <div class="heading">WHY <span style="color:var(--purple)">CHOOSE</span> <span class="soft">US</span></div>
  <div class="underline"></div>
  <p>Lighting design and application are paramount in our company's services.<br>Industry leading product use &amp; integration are always on the forefront with our customer client services.</p>
  <div class="link">SCHEDULE YOUR SERVICE TODAY</div>
</section>

<section class="contact-title abs">
  <div class="heading">GET IN <span class="soft">TOUCH</span></div>
  <div class="underline"></div>
</section>
<form class="contact-form">
  <div class="field" style="top:2704px;height:43px">Name<span class="req">*</span></div>
  <div class="field" style="top:2760px;height:43px">Phone</div>
  <div class="field" style="top:2814px;height:43px">Email<span class="req">*</span></div>
  <div class="field" style="top:2866px;height:84px">Message<span class="req">*</span></div>
  <span class="btn">SUBMIT</span>
</form>
<div class="contact-info abs">
  <h3>SCHEDULE YOUR SERVICE TODAY</h3>
  <div class="rule"></div>
  <p>CALL US : 555-014-2233</p>
  <p>OUR OFFICE :Street Name, City Name State Zipcode</p>
</div>
<div class="map abs" role="img" aria-label="Street map showing the office location"></div>

<footer class="site-footer abs">
  <nav class="footer-nav"><span>HOME</span><span>ABOUT US</span><span>GALLERY</span><span>CONTACT US</span></nav>
  <div class="company-name">K7 Electrical Services Ltd</div>
</footer>
<div class="copyright abs">Copyright ©2018 K7ElectricalServices. All Rights Reserved.</div>

</body>
</html>
```